Whitcombe Business Card Design

The name of the business is Dario Whitcombe, CPA LLC
The service that we offer is Accounting, Tax & Consulting Services. I need it to have the following items:
Dario Whitcombe, Principal
Phone Number
Email Address
Physical Address

I have attached the company logo, one in black and one in white. Please provide a design in black background and the other in white background. Please include "Accounting, Tax & Consulting Services". I want the business card to be clean and very professional.

```html
<!DOCTYPE html>
<html lang="en">
<head>
<meta charset="utf-8">
<title>Dario Whitcombe, CPA LLC – Business Card</title>
<link rel="stylesheet" href="https://fonts.googleapis.com/css2?family=Montserrat:wght@500;600;700&family=Roboto:wght@300;400&display=swap">
<style>
  :root {
    --backdrop: #2a2a2a;
    --card-dark: #232323;
    --card-dark-edge: #1c1c1c;
    --card-light: #f5f5f4;
    --card-light-edge: #e6e6e5;
    --ink-white: #f2f2f2;
    --ink-grey: #9a9a9a;
    --ink-body: #e4e4e4;
    --ink-dark: #1c1c1c;
    --accent-red: #a0181c;
  }
  * { margin: 0; padding: 0; box-sizing: border-box; }
  html, body {
    width: 1200px; height: 1138px; overflow: hidden;
    background: var(--backdrop);
  }
  .stage { position: relative; width: 1200px; height: 1138px; }
  .card {
    position: absolute;
    width: 620px; height: 376px;
    border-radius: 14px;
  }
  .card--front {
    left: 272px; top: 184px;
    background: linear-gradient(160deg, #fafaf9 0%, var(--card-light) 60%, var(--card-light-edge) 100%);
  }
  .card--back {
    left: 274px; top: 606px;
    background: linear-gradient(160deg, #262626 0%, var(--card-dark) 60%, var(--card-dark-edge) 100%);
  }

  .brand-name {
    position: absolute;
    display: flex; align-items: center; gap: 14px;
    font-family: "Montserrat", sans-serif;
    font-weight: 700;
    letter-spacing: 0.04em;
    text-transform: uppercase;
  }
  .brand-name__square { display: block; background: var(--accent-red); }
  .card--front .brand-name {
    left: 0; right: 0; top: 164px; justify-content: center;
    font-size: 38px; color: var(--ink-dark);
  }
  .card--front .brand-name__square { width: 34px; height: 34px; }
  .card--back .brand-name {
    left: 44px; top: 176px;
    font-size: 22px; color: var(--ink-white);
  }
  .card--back .brand-name__square { width: 20px; height: 20px; }

  .firm {
    position: absolute; left: 281px; top: 52px;
    font-family: "Montserrat", sans-serif;
  }
  .firm__name {
    font-size: 20px; font-weight: 600; color: var(--ink-white);
    text-transform: uppercase; letter-spacing: 0.01em; line-height: 24px;
  }
  .firm__tagline {
    font-size: 13.5px; font-weight: 600; color: var(--ink-grey);
    text-transform: uppercase; letter-spacing: 0.12em; line-height: 18px;
  }
  .firm__services {
    font-family: "Roboto", sans-serif;
    font-size: 13px; font-weight: 400; color: var(--ink-grey);
    line-height: 18px; margin-top: 2px;
  }
  .person { position: absolute; left: 281px; top: 132px; }
  .person__name {
    font-family: "Montserrat", sans-serif;
    font-size: 20px; font-weight: 600; color: var(--accent-red);
    text-transform: uppercase; letter-spacing: 0.03em; line-height: 24px;
  }
  .person__title {
    font-family: "Roboto", sans-serif; font-weight: 300;
    font-size: 16px; color: var(--ink-body); line-height: 20px;
  }
  .address {
    position: absolute; left: 281px; top: 204px;
    font-family: "Roboto", sans-serif; font-weight: 300; font-style: normal;
    font-size: 16px; line-height: 24px; color: var(--ink-body);
  }
  .contact {
    position: absolute; left: 281px; top: 258px; list-style: none;
    font-family: "Roboto", sans-serif; font-weight: 300;
    font-size: 16px; line-height: 24px; color: var(--ink-body);
  }
  .contact__item { display: flex; align-items: center; gap: 12px; }
  .contact__icon { width: 14px; height: 14px; fill: var(--accent-red); flex: none; }
</style>
</head>
<body>
<main class="stage">
  <section class="card card--front" aria-label="Card front, white version">
    <div class="brand-name"><span class="brand-name__square"></span>Whitcombe</div>
  </section>

  <section class="card card--back" aria-label="Card back, black version">
    <div class="brand-name"><span class="brand-name__square"></span>Whitcombe</div>

    <header class="firm">
      <p class="firm__name">Dario Whitcombe, CPA, LLC</p>
      <p class="firm__tagline">Certified Public Accountant</p>
      <p class="firm__services">Accounting, Tax &amp; Consulting Services</p>
    </header>

    <div class="person">
      <p class="person__name">Dario Whitcombe</p>
      <p class="person__title">Principal</p>
    </div>

    <address class="address">
      4870 Larkspur Avenue, Suite 210,<br>
      Brookfield, US 604512
    </address>

    <ul class="contact">
      <li class="contact__item">
        <svg class="contact__icon" viewBox="0 0 16 16" aria-hidden="true"><path d="M2 5c0-2 2-3 6-3s6 1 6 3v1h-3V5H5v1H2z M4 7h8l2 6H2z"/></svg>
        555-204-3178
      </li>
      <li class="contact__item">
        <svg class="contact__icon" viewBox="0 0 16 16" aria-hidden="true"><path d="M1 3h14v10H1z"/><path d="M1.5 3.5 8 8.5l6.5-5" stroke="#232323" stroke-width="1.2" fill="none"/></svg>
        dw@whitcombecpa.com
      </li>
      <li class="contact__item">
        <svg class="contact__icon" viewBox="0 0 16 16" aria-hidden="true"><circle cx="8" cy="8" r="7"/><path d="M1 8h14M8 1c-3 3-3 11 0 14M8 1c3 3 3 11 0 14" stroke="#232323" stroke-width="1" fill="none"/></svg>
        www.whitcombecpa.com
      </li>
    </ul>
  </section>
</main>
</body>
</html>
```